Vale Crest - Business Cards

We are a consultancy to help builders to optimize their planning in order to save building costs. For that reason we need a clean and professional business card for our high-priced services. A QR code should lead to the contact information needed.

```html
<!DOCTYPE html>
<html lang="en">
<head>
<meta charset="utf-8">
<title>Vale Crest - Business Cards</title>
<link href="https://fonts.googleapis.com/css2?family=Roboto:wght@400;500;700&display=swap" rel="stylesheet">
<style>
  :root {
    --backdrop: #2a2a2a;
    --gold-dark: #9a6220;
    --gold-mid: #c99a3e;
    --gold-light: #e8c267;
    --ink: #2b2b2b;
    --ink-soft: #3d3d3d;
    --paper: #f1f1f1;
    --paper-shade: #e2e2e2;
    --accent: #c9973a;
  }
  * { margin: 0; padding: 0; box-sizing: border-box; }
  html, body { width: 1200px; height: 1138px; overflow: hidden; }
  body {
    background: var(--backdrop);
    font-family: "Roboto", Arial, sans-serif;
    position: relative;
  }
  .card {
    position: absolute;
    border-radius: 16px;
    overflow: hidden;
  }
  .card--front {
    left: 274px; top: 186px; width: 623px; height: 376px;
    background: linear-gradient(45deg, var(--gold-dark) 0%, var(--gold-mid) 50%, var(--gold-light) 100%);
  }
  .card--back {
    left: 276px; top: 608px; width: 618px; height: 374px;
    background: linear-gradient(180deg, var(--paper) 0%, var(--paper-shade) 100%);
  }
  .brand-name {
    position: absolute;
    font-weight: 700;
    white-space: nowrap;
    letter-spacing: 2px;
    text-transform: uppercase;
    text-align: center;
  }
  .card--front .brand-name {
    left: 0; right: 0; top: 216px;
    font-size: 40px;
    line-height: 40px;
    color: var(--ink);
  }
  .card--back .brand-name {
    left: 40px; width: 296px; top: 218px;
    font-size: 28px;
    line-height: 32px;
    color: var(--accent);
  }
  .contact {
    position: absolute;
    left: 366px; top: 84px;
    color: var(--ink-soft);
  }
  .contact__name { font-size: 24px; font-weight: 500; color: var(--ink); line-height: 28px; }
  .contact__role { font-size: 16px; line-height: 22px; margin-bottom: 24px; }
  .contact__list { list-style: none; font-size: 17px; }
  .contact__list li { display: flex; align-items: center; height: 24px; }
  .contact__list svg { width: 14px; height: 14px; margin-right: 18px; fill: var(--accent); }
  .contact__address { font-size: 17px; line-height: 24px; margin-top: 6px; }
</style>
</head>
<body>
  <section class="card card--front">
    <div class="brand-name">Vale Crest</div>
  </section>

  <section class="card card--back">
    <div class="brand-name">Vale Crest</div>
    <div class="contact">
      <div class="contact__name">Vale Crest</div>
      <div class="contact__role">Managing Director</div>
      <ul class="contact__list">
        <li>
          <svg viewBox="0 0 16 16" aria-hidden="true"><path d="M1 5c0-2 3-3 7-3s7 1 7 3v1h-3V5H4v1H1z M3 7h10l1 7H2z"/></svg>
          555-014-2290
        </li>
        <li>
          <svg viewBox="0 0 16 16" aria-hidden="true"><path d="M1 3h14v10H1z M2 4l6 5 6-5" stroke="#f1f1f1" stroke-width="1"/></svg>
          hello@valecrest.example
        </li>
        <li>
          <svg viewBox="0 0 16 16" aria-hidden="true"><circle cx="8" cy="8" r="7"/><path d="M1 8h14M8 1v14M3 4h10M3 12h10" stroke="#f1f1f1" stroke-width="0.8" fill="none"/></svg>
          www.valecrest.example
        </li>
      </ul>
      <div class="contact__address">48 Ridge Lane, Brookfield,<br>Northvale, US 204518</div>
    </div>
  </section>
</body>
</html>
```